2018 TVPAC Conference Theme Artwork

We need artwork designed around the theme of this year's human resources conference. The theme is "Celebrating 20 Years Together Towards Tomorrow". The artwork should be designed as a 4x6 postcard and will eventually be adapted/reformatted to use on the registration website, sales materials, e-newsletters, conference guide cover and signage.

Target Market(s)

Attendees are human resources professionals. Exhibitors and sponsors are companies who want to sell their products/services to human resource professionals

Colors

Designer to choose colors to be used in the design.

Requirements
Must have
• NO BORING PIXVAULT IMAGERY PLEASE.
• Theme: Celebrating 20 Years Together Towards Tomorrow
• Event: 20th Annual TVPA Conference
• Dates/Times: Tuesday, May 15, 2018, 12:30pm - 5:00pm and Wednesday, May 16, 2018 7:30am - 5:30pm
• Website: tvpaconference.example
• Location: The HALL at the Corvane Manchester
Nice to have
• Engaging, celebratory, visually attractive
Should not have
• NO BORING PIXVAULT IMAGERY.

```html
<!DOCTYPE html>
<html lang="en">
<head>
<meta charset="utf-8">
<title>20th Annual TVPA Conference Postcard</title>
<link rel="stylesheet" href="https://fonts.googleapis.com/css2?family=Oswald:wght@600;700&family=Open+Sans:wght@400;600;700&display=swap">
<style>
  :root {
    --navy: #1d4f7c;
    --navy-dark: #173f63;
    --gold: #f6b21b;
    --white: #ffffff;
    --ink: #2b2b2b;
    --rule: #8a8a8a;
    --page: #eeeeee;
    --photo-light: #e9e6e2;
    --photo-mid: #8d8a88;
  }
  * { box-sizing: border-box; margin: 0; padding: 0; }
  html, body { width: 996px; height: 1200px; overflow: hidden; }
  body { background: var(--page); font-family: "Open Sans", sans-serif; position: relative; }

  .postcard {
    position: absolute; left: 138px; width: 720px; height: 480px;
    background: var(--white); overflow: hidden;
    box-shadow: 0 4px 14px rgba(0,0,0,0.18);
  }
  .postcard--front { top: 90px; }
  .postcard--back { top: 630px; }

  /* Front */
  .front-band {
    position: absolute; left: 0; top: 0; width: 100%; height: 142px;
    background: var(--navy); padding: 16px 36px;
  }
  .theme-line {
    font-family: "Oswald", sans-serif; font-weight: 700; color: var(--white);
    font-size: 38px; line-height: 42px; letter-spacing: 0.5px;
  }
  .theme-line--second { font-size: 33px; line-height: 38px; }
  .event-name {
    font-family: "Open Sans", sans-serif; font-weight: 700; color: var(--gold);
    font-size: 25px; line-height: 34px;
  }
  .org-name {
    position: absolute; right: 34px; top: 38px; color: var(--white);
    font-weight: 700; font-size: 24px;
    display: flex; align-items: center; gap: 10px;
  }
  .org-name__mark { width: 14px; height: 14px; background: var(--white); border-radius: 50%; }
  .web-pill {
    position: absolute; right: 0; top: 142px; background: var(--gold); color: var(--navy-dark);
    font-weight: 600; font-size: 18px; padding: 4px 18px 6px 22px;
    border-radius: 0 0 0 18px; z-index: 2;
  }
  .front-photo {
    position: absolute; left: 112px; top: 160px; width: 500px; height: 300px;
    background: linear-gradient(180deg, var(--white) 0%, var(--photo-light) 40%, var(--photo-mid) 100%);
  }

  /* Back */
  .back-shapes { position: absolute; left: 0; top: 0; }
  .back-org {
    position: absolute; left: 60px; top: 40px; color: var(--white);
    font-weight: 700; font-size: 24px; display: flex; align-items: center; gap: 10px;
  }
  .back-org__mark { width: 14px; height: 14px; background: var(--white); border-radius: 50%; }
  .schedule { position: absolute; left: 10px; top: 140px; display: flex; }
  .schedule__col { padding: 0 12px; }
  .schedule__col + .schedule__col { border-left: 1.5px solid var(--rule); }
  .schedule__label {
    display: inline-flex; align-items: center; gap: 6px; background: var(--navy); color: var(--white);
    font-weight: 700; font-size: 17px; padding: 1px 12px; border-radius: 5px; margin-bottom: 4px;
  }
  .schedule__label-icon { width: 14px; height: 14px; }
  .schedule__item { font-size: 14px; line-height: 29px; color: var(--ink); }
  .venue {
    position: absolute; left: 18px; top: 242px; display: flex; align-items: center; gap: 7px;
    color: var(--navy); font-weight: 700; font-size: 14.5px;
  }
  .address-line { position: absolute; left: 445px; width: 258px; height: 1.5px; background: var(--rule); }
  .stamp-box { position: absolute; left: 603px; top: 28px; width: 100px; height: 100px; border: 1.5px solid var(--rule); }
</style>
</head>
<body>

<section class="postcard postcard--front">
  <div class="front-photo" role="img" aria-label="Photo of a cheering group of business professionals in suits raising their fists"></div>
  <header class="front-band">
    <p class="theme-line">CELEBRATING 20 YEARS</p>
    <p class="theme-line theme-line--second">TOGETHER TOWARDS TOMORROW</p>
    <p class="event-name">20th Annual TVPA Conference</p>
    <div class="org-name"><span class="org-name__mark"></span>TVPA Council</div>
  </header>
  <p class="web-pill">tvpaconference.example</p>
</section>

<section class="postcard postcard--back">
  <svg class="back-shapes" width="720" height="480" viewBox="0 0 720 480">
    <defs>
      <clipPath id="info-area">
        <path d="M0,118 H330 C375,150 372,340 258,480 H0 Z"/>
      </clipPath>
      <linearGradient id="team-photo-tone" x1="0" y1="0" x2="1" y2="1">
        <stop offset="0" stop-color="#cfd3d6"/>
        <stop offset="0.5" stop-color="#b9a89a"/>
        <stop offset="1" stop-color="#5b6670"/>
      </linearGradient>
    </defs>
    <rect x="0" y="278" width="400" height="202" fill="url(#team-photo-tone)" clip-path="url(#info-area)" role="img" aria-label="Photo of a team of colleagues working together around a laptop"/>
    <path d="M305,0 H330 C430,120 430,330 340,440 C395,320 395,130 305,0 Z" fill="var(--gold)"/>
    <path d="M0,0 H290 C400,110 395,340 290,480 H258 C372,340 375,150 330,118 H0 Z" fill="var(--navy)"/>
  </svg>

  <div class="back-org"><span class="back-org__mark"></span>TVPA Council</div>

  <div class="schedule">
    <div class="schedule__col">
      <span class="schedule__label">Date
        <svg class="schedule__label-icon" viewBox="0 0 14 14"><rect x="1" y="2" width="12" height="11" fill="none" stroke="#fff" stroke-width="1.5"/><line x1="1" y1="5.5" x2="13" y2="5.5" stroke="#fff" stroke-width="1.5"/></svg>
      </span>
      <p class="schedule__item">Tuesday, May 15, 2018,</p>
      <p class="schedule__item">Wednesday, May 16, 2018</p>
    </div>
    <div class="schedule__col">
      <span class="schedule__label">Time
        <svg class="schedule__label-icon" viewBox="0 0 14 14"><circle cx="7" cy="7.5" r="5.5" fill="none" stroke="#fff" stroke-width="1.5"/><path d="M7,4.5 V7.5 H9.5" fill="none" stroke="#fff" stroke-width="1.5"/></svg>
      </span>
      <p class="schedule__item">12:30pm - 5:00pm</p>
      <p class="schedule__item">7:30am - 5:30pm</p>
    </div>
  </div>

  <p class="venue">
    <svg width="13" height="17" viewBox="0 0 13 17"><path d="M6.5,0.8 C3.4,0.8 1,3.2 1,6.2 C1,10.2 6.5,16 6.5,16 C6.5,16 12,10.2 12,6.2 C12,3.2 9.6,0.8 6.5,0.8 Z" fill="var(--navy)"/><circle cx="6.5" cy="6.2" r="2.2" fill="#fff"/></svg>
    The HALL at the Corvane Manchester
  </p>

  <div class="stamp-box"></div>
  <div class="address-line" style="top:275px"></div>
  <div class="address-line" style="top:322px"></div>
  <div class="address-line" style="top:368px"></div>
</section>

</body>
</html>
```